IT solutions & services company requires stationary makeover

Looking for a consistent modern, professional design across our printed client touch points:
Business Cards
Letterhead
Client proposal
Flyer
Postcard

We provide solutions for SME IT - servers, backups, AV etc, and the ongoing services around them.
we are happy with our logo - please see attached and would like the colour theme to be maintained.

```html
<!DOCTYPE html>
<html lang="en">
<head>
<meta charset="utf-8">
<title>Kestrel — Letterhead</title>
<link rel="stylesheet" href="https://fonts.googleapis.com/css2?family=Arimo:ital,wght@0,400;0,700;1,400;1,700&display=swap">
<style>
  :root {
    --backdrop: #e6e6e4;
    --paper: #ffffff;
    --ink: #2b2b2b;
    --ink-soft: #3a3a3a;
    --brand-blue: #1a86aa;
    --accent-pale: #bcdde8;
    --accent-grey: #c4c4c4;
  }
  * { box-sizing: border-box; margin: 0; padding: 0; }
  html, body {
    width: 1055px;
    height: 1200px;
    overflow: hidden;
    background: var(--backdrop);
    font-family: "Arimo", Arial, sans-serif;
    color: var(--ink);
  }
  .letterhead {
    position: absolute;
    left: 124px;
    top: 30px;
    width: 806px;
    height: 1140px;
    background: var(--paper);
    overflow: hidden;
    box-shadow: 0 2px 10px rgba(0,0,0,0.12);
  }
  .brand {
    position: absolute;
    left: 42px;
    top: 44px;
  }
  .brand-row {
    display: flex;
    align-items: center;
    gap: 14px;
  }
  .brand-dot {
    width: 46px;
    height: 46px;
    border-radius: 50%;
    background: var(--brand-blue);
  }
  .brand-name {
    font-size: 52px;
    font-weight: 400;
    color: var(--ink);
    letter-spacing: 0.5px;
    line-height: 1;
  }
  .brand-tagline {
    margin-top: 8px;
    margin-left: 74px;
    font-size: 12.5px;
    letter-spacing: 0.6px;
    color: var(--ink-soft);
  }
  .contact {
    position: absolute;
    right: 44px;
    top: 42px;
    text-align: right;
    font-style: italic;
    font-size: 13px;
    line-height: 17px;
    color: var(--ink-soft);
  }
  .contact .web {
    font-weight: 700;
    color: var(--ink);
  }
  .decor {
    position: absolute;
    right: -60px;
    bottom: 70px;
    width: 420px;
    height: 420px;
  }
</style>
</head>
<body>
  <main class="letterhead">
    <header class="brand">
      <div class="brand-row">
        <span class="brand-dot"></span>
        <span class="brand-name">Kestrel</span>
      </div>
      <p class="brand-tagline">TECHNOLOGY MADE SIMPLE</p>
    </header>

    <address class="contact">
      03 555 0182<br>
      alee@kestrel-it.example.com<br>
      Level 2,<br>
      Harbour Lane,<br>
      Lyttelton, NZ<br>
      <span class="web">www.kestrel-it.example.com</span>
    </address>

    <svg class="decor" viewBox="0 0 420 420" aria-hidden="true">
      <defs>
        <radialGradient id="decor-fill" cx="50%" cy="45%" r="55%">
          <stop offset="0%" stop-color="#d6eef5"/>
          <stop offset="100%" stop-color="#a9cbd8"/>
        </radialGradient>
      </defs>
      <circle cx="210" cy="210" r="200" fill="url(#decor-fill)" opacity="0.75"/>
    </svg>
  </main>
</body>
</html>
```